Natural Light/Organic/Documentary Photography Business

I like a simple, approachable, feminine, earthy/organic feel. Earth/neutral tones, nothing too loud or obnoxious. I like the watercolor look. I don't want anything too trendy or something I'll get tired of after a couple months. As far as colors, I am much more a fan of cream/taupe/blue/green...not a fan of pink or purple at all.

Target Market(s)

Weddings & Families

Industry/Entity Type

Wedding Photography

Contact Information for Business Card

website, email, phone number

Font styles to use
Other font styles liked:
• Horizontes, Gotham

Colors

Designer to choose colors to be used in the design.

Requirements
Must have
• Website: www.mirelhatchway.com
• Phone: 418.629.5073
• Email: mirel@mirelhatchway.com
Nice to have
• I like the watercolor look but its not necessary. I like simple/earthy tones. Nothing too loud or distracting. Simple & feminine without being too girly. I like an approachable/soft feel.
• Instagram: www.instagram.com/mirelhatchwayphotography/
Should not have
• NO loud colors or design or pattern. I do not want a photo of a camera or lens or anything cheesy like that.

```html
<!DOCTYPE html>
<html lang="en">
<head>
<meta charset="utf-8">
<title>Mirel Hatchway Photography — Business Card</title>
<link rel="stylesheet" href="https://fonts.googleapis.com/css2?family=Allura&family=Montserrat:wght@400&family=Spectral:wght@400&display=swap">
<style>
  :root {
    --paper-top: #f9f9fc;
    --paper-cream: #fdf9ec;
    --wash-green: #9ff0c4;
    --wash-mint: #c8f6e0;
    --wash-tan: #e6d9aa;
    --wash-umber: #b9ab80;
    --ink: #141414;
    --ink-soft: #2a2a2a;
  }
  * { margin: 0; padding: 0; box-sizing: border-box; }
  html, body {
    width: 1200px;
    height: 678px;
    overflow: hidden;
    background: var(--paper-top);
  }
  .card {
    position: relative;
    width: 1200px;
    height: 678px;
    overflow: hidden;
    background: linear-gradient(to bottom, var(--paper-top) 0, var(--paper-top) 235px, var(--paper-cream) 235px, var(--paper-cream) 100%);
  }
  .watercolor-wash {
    position: absolute;
    inset: 0;
    width: 1200px;
    height: 678px;
  }
  .brand {
    position: absolute;
    top: 120px;
    left: 0;
    width: 100%;
    text-align: center;
  }
  .brand-name {
    font-family: "Allura", cursive;
    font-weight: 400;
    font-size: 118px;
    line-height: 1;
    color: var(--ink);
    margin-left: 24px;
  }
  .brand-tagline {
    font-family: "Montserrat", sans-serif;
    font-size: 17px;
    letter-spacing: 14px;
    color: var(--ink);
    margin-top: -2px;
    margin-left: 36px;
  }
  .contact-list {
    position: absolute;
    top: 356px;
    left: 0;
    width: 100%;
    list-style: none;
    text-align: center;
    font-family: "Spectral", serif;
    font-variant: small-caps;
    font-size: 18px;
    color: var(--ink-soft);
  }
  .contact-item {
    height: 50.5px;
    margin-left: -6px;
  }
  .contact-item .contact-label { margin-right: 4px; }
</style>
</head>
<body>
<main class="card">
  <svg class="watercolor-wash" viewBox="0 0 1200 678" role="img" aria-label="Soft watercolor wash in mint green fading into sandy tan">
    <defs>
      <linearGradient id="wash-fill" x1="0" y1="0" x2="0" y2="1">
        <stop offset="0" stop-color="var(--wash-mint)"/>
        <stop offset="0.45" stop-color="var(--wash-green)"/>
        <stop offset="0.72" stop-color="var(--wash-tan)"/>
        <stop offset="1" stop-color="var(--wash-umber)"/>
      </linearGradient>
      <filter id="wash-soften" x="-10%" y="-10%" width="120%" height="120%">
        <feGaussianBlur stdDeviation="18"/>
      </filter>
    </defs>
    <path d="M190 150 C330 95 560 85 760 100 C900 110 1020 130 1050 200 C1070 300 1040 420 1060 520 C1070 600 1075 650 1070 678 L120 678 C115 600 130 520 125 450 C120 360 150 230 190 150 Z"
          fill="url(#wash-fill)" opacity="0.85" filter="url(#wash-soften)"/>
  </svg>

  <header class="brand">
    <h1 class="brand-name">Mirel Hatchway</h1>
    <p class="brand-tagline">PHOTOGRAPHY</p>
  </header>

  <ul class="contact-list">
    <li class="contact-item"><span class="contact-label">Cell:</span>418.629.5073</li>
    <li class="contact-item"><span class="contact-label">Email:</span>mirel@mirelhatchway.com</li>
    <li class="contact-item"><span class="contact-label">Web:</span>www.mirelhatchway.com</li>
    <li class="contact-item"><span class="contact-label">Insta:</span>@mirelhatchwayphotography</li>
  </ul>
</main>
</body>
</html>
```